New Mechanical Maintenance business needs website

New Mechanical Maintenance business in Perth Western Australia needs a nice and easy to navigate website. Showing what we do and how we can be the right fit for other small to medium size business by offering personalized service from our highly skilled team. We deal with both fixed plant repairs like food and chemical processing facilities to heavy equipment like drill rigs, Large boats and earthmoving equipment.

Target Market(s)

Small to medium business to offer personalized services/packages

Industry/Entity Type

e deal with both fixed plant repairs like food and chemical processing facilities to heavy equipment like drill rigs, Large boats and earthmoving equipment.

Coding

Coded - Design and coding required

Number of Pages Required

4 page

Font styles to use
Serif

Colors
0054AA
0677BA
7BADD7
CADEEF
E8F1F8

Requirements
Must have
• A website that is easy to navigate but covers off on the range of services/maintenance we can provide

```html
<!DOCTYPE html>
<html lang="en">
<head>
<meta charset="utf-8">
<title>KVR Maintenance Services</title>
<link href="https://fonts.googleapis.com/css2?family=Russo+One&family=Poppins:wght@400;500;600;700&display=swap" rel="stylesheet">
<style>
:root{
  --blue:#003f8a;
  --blue-mid:#0054aa;
  --ink:#1a1a1a;
  --black:#0a0a0a;
  --light:#e5ecf3;
  --grey:#555;
  --orange:#f26522;
  --white:#fff;
}
*{margin:0;padding:0;box-sizing:border-box}
html,body{width:1200px;height:3828px;overflow:hidden}
body{position:relative;font-family:"Poppins",sans-serif;color:var(--ink);background:var(--white)}
.abs{position:absolute}
.head{font-family:"Russo One",sans-serif;letter-spacing:1px}
.btn{position:absolute;display:flex;align-items:center;justify-content:center;font-family:"Russo One",sans-serif;font-size:17px;color:var(--white);background:var(--blue);border-radius:3px;letter-spacing:.5px}
.btn.grey{background:#555}
.topbar{left:0;top:0;width:1200px;height:41px;background:var(--black);color:#fff;font-size:13px;display:flex;align-items:center;justify-content:center;padding-left:120px}
.logo{left:111px;top:0;width:134px;height:116px;background:#fff;border-radius:50%;border:8px solid #555;display:flex;align-items:center;justify-content:center;font-family:"Russo One",sans-serif;font-size:26px;color:#333;letter-spacing:3px}
.callus{left:852px;top:50px;font-family:"Russo One",sans-serif}
.callus .small{font-size:17px;color:#111}
.callus .num{font-size:24px;color:var(--blue);letter-spacing:1px}
.nav{left:0;top:122px;width:1200px;height:41px;background:var(--black)}
.nav-blue{left:0;top:122px;width:906px;height:41px;background:var(--blue);clip-path:polygon(0 0,100% 0,94% 100%,0 100%)}
.nav a{position:absolute;top:133px;color:#fff;font-size:13.5px;text-decoration:none}
.nav-home{left:122px;top:127px;width:64px;height:31px;border:1px solid #ccc;background:#2a2a2a;border-radius:3px;color:#fff;font-size:13.5px;display:flex;align-items:center;justify-content:center}
.soc{width:30px;height:30px;background:#555;display:flex;align-items:center;justify-content:center;color:#fff;font-size:14px}
.hero{left:0;top:163px;width:1200px;height:700px;background:linear-gradient(180deg,#8fa6c4 0%,#e6a07e 22%,#c1714e 32%,#3a4256 52%,#1e2a3a 75%,#25384a 100%)}
.hero-title{left:0;top:208px;width:1200px;text-align:center;font-family:"Russo One",sans-serif;font-size:44px;color:#111;letter-spacing:3px}
.dot{width:11px;height:11px;border:1.5px solid #fff;border-radius:50%}
.eyebrow{font-family:"Russo One",sans-serif;font-size:16px;letter-spacing:5px;color:var(--blue)}
.h2{font-family:"Russo One",sans-serif;font-size:42px;color:#111;letter-spacing:1.5px;line-height:1.05;padding-left:12px;border-left:6px solid var(--blue)}
.about-text{left:616px;top:1102px;width:468px;font-size:17.5px;line-height:29px;text-align:justify;color:#222}
.why{left:0;top:1494px;width:1200px;height:408px;background:var(--light)}
.col{top:1675px;width:320px;height:134px;border-left:2px solid #888;padding-left:20px}
.col .n{position:absolute;left:20px;top:-4px;font-family:"Russo One",sans-serif;font-size:46px;color:var(--blue)}
.col .t{position:absolute;left:68px;top:6px;font-family:"Russo One",sans-serif;font-size:15.5px;line-height:20px;color:#111}
.col .p{position:absolute;left:20px;top:64px;width:295px;font-size:12.5px;line-height:22px;color:#555;text-align:justify}
.services{left:0;top:1902px;width:1200px;height:927px;background:var(--blue)}
.svc-img{top:2158px;width:304px;height:228px}
.svc-title{top:2425px;font-family:"Russo One",sans-serif;font-size:25px;line-height:30px;color:#fff}
.svc-line{top:2503px;width:92px;height:2px;background:#fff}
.svc-text{top:2527px;width:315px;font-size:14px;line-height:24px;color:#fff}
.svc-more{top:2632px;font-family:"Russo One",sans-serif;font-size:15px;color:#fff;text-decoration:underline;display:flex;align-items:center;gap:10px}
.qmark{font-family:"Russo One",sans-serif;font-size:140px;color:#cfd6df;line-height:1}
.footer h4{position:absolute;font-family:"Russo One",sans-serif;font-size:18px;color:#fff;letter-spacing:.5px}
.footer h4::after{content:"";position:absolute;left:0;top:34px;width:48px;height:2px;background:#fff}
.flink{position:absolute;font-size:12px;color:#fff;line-height:26px}
.ci{position:absolute;left:799px;width:36px;height:36px;border-radius:50%;background:var(--blue);display:flex;align-items:center;justify-content:center}
.ctext{position:absolute;left:852px;font-size:13px;line-height:19px;color:#fff}
.ctext span{color:#aaa;display:block}
</style>
</head>
<body>

<!-- Top bar -->
<div class="abs topbar">Call us today on +1 (555) 014-2290 for a free onsite quotation or email info@kvrmaintenance.com</div>

<!-- Header -->
<div class="btn" style="left:499px;top:56px;width:126px;height:46px">CONTACT US</div>
<div class="btn grey" style="left:679px;top:56px;width:159px;height:46px;font-size:16px">EMPLOYEE LOGIN</div>
<div class="abs callus"><div class="small">CALL US TODAY!</div><div class="num">+1 (555) 014-2290</div></div>

<!-- Nav -->
<div class="abs nav"></div>
<div class="abs nav-blue"></div>
<div class="abs nav-home">HOME</div>
<nav class="nav">
  <a style="left:217px">OUR SERVICES</a>
  <a style="left:355px">ABOUT US</a>
  <a style="left:465px">WHY CHOOSE US</a>
  <a style="left:618px">WHERE WE COME FROM</a>
</nav>
<div class="abs soc" style="left:1017px;top:127px">f</div>
<div class="abs soc" style="left:1054px;top:127px">▶</div>

<!-- Hero -->
<div class="abs hero" role="img" aria-label="Perth city skyline at sunset over the river"></div>
<div class="abs hero-title">KVR MAINTENANCE SERVICES PTY LTD</div>
<div class="btn" style="left:443px;top:291px;width:152px;height:46px">CONTACT US</div>
<div class="btn grey" style="left:606px;top:291px;width:151px;height:46px">GET A QUOTE</div>
<div class="abs dot" style="left:47px;top:393px"></div>
<div class="abs dot" style="left:47px;top:411px;background:var(--blue)"></div>
<div class="abs dot" style="left:47px;top:429px"></div>
<div class="abs dot" style="left:47px;top:447px"></div>
<svg class="abs" style="left:0;top:700px" width="1200" height="180">
  <polygon points="0,10 928,163 1200,13 1200,180 0,180" fill="#fff"/>
  <polygon points="356,72 928,163 1092,72 928,153" fill="#003f8a"/>
</svg>

<!-- Logo above hero line -->
<div class="abs logo">KVR</div>

<!-- About -->
<div class="abs" style="left:85px;top:995px;width:473px;height:405px;border:2px solid var(--blue)"></div>
<div class="abs" style="left:111px;top:961px;width:474px;height:405px;background:linear-gradient(135deg,#6c6f74,#a3a6aa 45%,#4a4d52);border-bottom:4px solid var(--orange)" role="img" aria-label="Crew working on a drilling rig floor"></div>
<div class="abs eyebrow" style="left:638px;top:976px">ORIGIN STORY</div>
<div class="abs h2" style="left:616px;top:1002px">WHERE WE<br>COME FROM</div>
<p class="abs about-text">Director of the company has over 20-year experience in the fixed and mobile plant industries ranging from Perth local and overseas. Facilities like precious metals refining, offshore drilling and production platform, open cut and underground mining, civils, geotechnical and construction equipment and large-scale construction as an expat overseas.</p>
<div class="btn" style="left:618px;top:1332px;width:153px;height:46px">LEARN MORE</div>

<!-- Why choose us -->
<div class="abs why"></div>
<div class="abs eyebrow" style="left:0;top:1557px;width:1200px;text-align:center">REASONS TO SELECT US</div>
<div class="abs h2" style="left:410px;top:1580px">WHY CHOOSE US</div>
<div class="abs col" style="left:111px"><div class="n">1.</div><div class="t">VOLUPTATEM ACCUSANTIUM<br>DOLOREMQUE LAUD.</div><div class="p">Werspiciatis aseeunde omnis iste natus error sitvolasuptate masease accusantium dolorem quelaudtium, totam rem aperiam.</div></div>
<div class="abs col" style="left:441px"><div class="n">2.</div><div class="t">VOLUPTATEM ACCUSANTIUM<br>DOLOREMQUE LAUD.</div><div class="p">Werspiciatis aseeunde omnis iste natus error sitvolasuptate masease accusantium dolorem quelaudtium, totam rem aperiam.</div></div>
<div class="abs col" style="left:774px"><div class="n">3.</div><div class="t">VOLUPTATEM ACCUSANTIUM<br>DOLOREMQUE LAUD.</div><div class="p">Werspiciatis aseeunde omnis iste natus error sitvolasuptate masease accusantium dolorem quelaudtium, totam rem aperiam.</div></div>

<!-- Services -->
<div class="abs services"></div>
<div class="abs eyebrow" style="left:0;top:2000px;width:1200px;text-align:center;color:#fff">WHAT WE DO</div>
<div class="abs h2" style="left:432px;top:2024px;color:#fff;border-color:#fff;font-size:40px">OUR SERVICES</div>
<p class="abs" style="left:0;top:2084px;width:1200px;text-align:center;font-size:15px;line-height:25px;color:#fff">Kaerspiciatis unde omnis iste natus error sit voluptatem accusantium doloremque<br>laudantium, totam rem aperiam, eaque ipsa quae ab illo inventore</p>

<div class="abs svc-img" style="left:101px;background:linear-gradient(135deg,#2b2f36,#6a6560 50%,#1d2026)" role="img" aria-label="Mechanic grinding a metal part in a workshop"></div>
<div class="abs svc-img" style="left:444px;background:linear-gradient(135deg,#3a3a3e,#7a6c60 50%,#2a2b30)" role="img" aria-label="Mechanic repairing an engine"></div>
<div class="abs svc-img" style="left:789px;background:linear-gradient(135deg,#40454c,#6b7078 50%,#2a2d32)" role="img" aria-label="Mechanic using a tablet beside machinery"></div>

<div class="abs svc-title" style="left:98px">EIUSMOD TEMPOR<br>INCIDIDUNT</div>
<div class="abs svc-title" style="left:442px">EIUSMOD TEMPOR<br>INCIDIDUNT</div>
<div class="abs svc-title" style="left:786px">EIUSMOD TEMPOR<br>INCIDIDUNT</div>
<div class="abs svc-line" style="left:99px"></div>
<div class="abs svc-line" style="left:443px"></div>
<div class="abs svc-line" style="left:787px"></div>
<p class="abs svc-text" style="left:99px">Karspiciatis unde omnis iste natus error sit voluptatem accusantium doloremque laudantium, totam rem aperiam, eaque ipsa quae ab illo inventore.</p>
<p class="abs svc-text" style="left:443px">Karspiciatis unde omnis iste natus error sit voluptatem accusantium doloremque laudantium, totam rem aperiam, eaque ipsa quae ab illo inventore.</p>
<p class="abs svc-text" style="left:787px">Karspiciatis unde omnis iste natus error sit voluptatem accusantium doloremque laudantium, totam rem aperiam, eaque ipsa quae ab illo inventore.</p>
<div class="abs svc-more" style="left:99px">Learn more <svg width="46" height="10"><path d="M0 5H44M38 1l6 4-6 4" stroke="#fff" fill="none" stroke-width="1.5"/></svg></div>
<div class="abs svc-more" style="left:443px">Learn more <svg width="46" height="10"><path d="M0 5H44M38 1l6 4-6 4" stroke="#fff" fill="none" stroke-width="1.5"/></svg></div>
<div class="abs svc-more" style="left:787px">Learn more <svg width="46" height="10"><path d="M0 5H44M38 1l6 4-6 4" stroke="#fff" fill="none" stroke-width="1.5"/></svg></div>
<div class="btn" style="left:524px;top:2695px;width:153px;height:46px;background:#fff;color:#111">VIEW MORE</div>

<!-- Reviews -->
<div class="abs qmark" style="left:90px;top:2925px">“</div>
<div class="abs qmark" style="left:1010px;top:3140px">”</div>
<div class="abs eyebrow" style="left:0;top:2928px;width:1200px;text-align:center">TESTIMONIALS</div>
<div class="abs h2" style="left:497px;top:2950px">REVIEWS</div>
<p class="abs" style="left:170px;top:3014px;width:860px;text-align:center;font-size:15px;line-height:25px;color:#333">“Garspiciatis unde omnis iste natus error sit voluptatem accusantium doloremque laudantium, totam rem aperiam, eaque ipsa quae ab illo inventore veritatis et quasi architecto beatae vitae dicta sunt explicabo. Nemo enim ipsam voluptatem quia voluptas sit aspernatur aut odit”</p>
<div class="abs" style="left:588px;top:3104px;width:28px;height:3px;background:var(--blue)"></div>
<div class="abs head" style="left:0;top:3117px;width:1200px;text-align:center;font-size:24px;color:#111">CAROL ANN WHITFIELD</div>
<div class="abs" style="left:0;top:3146px;width:1200px;text-align:center;font-size:18px;color:var(--orange);letter-spacing:2px">★★★★★</div>
<div class="abs dot" style="left:572px;top:3201px;border-color:#555;width:9px;height:9px"></div>
<div class="abs dot" style="left:589px;top:3198px;border-color:var(--blue);background:var(--blue);width:13px;height:13px"></div>
<div class="abs dot" style="left:607px;top:3201px;border-color:#555;width:9px;height:9px"></div>
<div class="abs dot" style="left:623px;top:3201px;border-color:#555;width:9px;height:9px"></div>

<!-- Footer -->
<svg class="abs" style="left:0;top:3280px" width="1200" height="480">
  <polygon points="0,165 275,14 839,103 1200,120 1200,480 0,480" fill="#0a0a0a"/>
  <polygon points="108,97 272,0 839,103 272,12" fill="#003f8a"/>
</svg>
<div class="footer">
  <div class="abs logo" style="left:198px;top:3482px;width:128px;height:104px;border-color:#fff;background:#0a0a0a;color:#fff;font-size:26px">KVR</div>
  <div class="abs soc" style="left:205px;top:3612px">f</div>
  <div class="abs soc" style="left:247px;top:3612px">▶</div>
  <h4 style="left:419px;top:3462px">QUICK LINKS</h4>
  <div class="flink" style="left:420px;top:3515px">HOME<br>ROOFING<br>CONSTRUCTION SERVICES<br>ABOUT US<br>GALLERY<br>AREAS WE SERVE<br>CONTACT US</div>
  <h4 style="left:645px;top:3462px">LINKS</h4>
  <div class="flink" style="left:646px;top:3515px">COPYRIGHT<br>LEGAL<br>PRIVACY<br>ACCESSIBILITY<br>SITEMAP</div>
  <h4 style="left:799px;top:3462px">CONTACT US</h4>
  <div class="ci" style="top:3512px"><svg width="16" height="18"><path d="M8 1a6 6 0 0 0-6 6c0 5 6 10 6 10s6-5 6-10a6 6 0 0 0-6-6zm0 8a2 2 0 1 1 0-4 2 2 0 0 1 0 4z" fill="#fff"/></svg></div>
  <div class="ctext" style="top:3514px"><span>Address</span>1482 Ridgeline Road<br>Easton, IN 47010</div>
  <div class="ci" style="top:3590px"><svg width="16" height="16"><path d="M3 1l3 0 1 4-2 1c1 2 3 4 5 5l1-2 4 1v3c0 1-1 2-2 2C7 15 1 9 1 3c0-1 1-2 2-2z" fill="#fff"/></svg></div>
  <div class="ctext" style="top:3592px"><span>Call Us</span>+1 (555) 014-2290</div>
  <div class="ci" style="top:3650px"><svg width="16" height="16"><path d="M3 1l3 0 1 4-2 1c1 2 3 4 5 5l1-2 4 1v3c0 1-1 2-2 2C7 15 1 9 1 3c0-1 1-2 2-2z" fill="#fff"/></svg></div>
  <div class="ctext" style="top:3650px"><span>Email</span>info@kvrmaintenance.com</div>
</div>
<div class="abs" style="left:0;top:3757px;width:1200px;height:71px;background:var(--blue)"></div>
<div class="abs" style="left:0;top:3775px;width:1200px;text-align:center;color:#fff;font-size:14px;font-weight:600">©2024. All rights reserved.</div>
<div class="abs" style="left:1113px;top:3731px;width:44px;height:44px;border-radius:50%;background:var(--blue);display:flex;align-items:center;justify-content:center"><svg width="14" height="10"><path d="M2 8l5-5 5 5" stroke="#fff" stroke-width="2" fill="none"/></svg></div>

</body>
</html>
```